Income Tax Business Cards - Updates

Need to update these business cards while keeping all the same wording but just update them and make them look nicer and more modern/ on brand with our brand.

Industry/Entity Type

finance

Contact Information for Business Card

we have multiple locations so will just need to easily be able to change the address and phone numbers

Colors

Designer to choose colors to be used in the design.

```html
<!DOCTYPE html>
<html lang="en">
<head>
<meta charset="utf-8">
<title>Tax Advance Business Card</title>
<link href="https://fonts.googleapis.com/css2?family=Montserrat:wght@600;700;800&family=Lato:wght@400;700&display=swap" rel="stylesheet">
<style>
  :root {
    --green: #10573a;
    --green-deep: #0a4026;
    --red: #b81d24;
    --ink: #262626;
    --text: #3a3a3a;
    --paper: #f6f6f6;
    --bg: #ece8e4;
    --white: #ffffff;
  }
  * { margin: 0; padding: 0; box-sizing: border-box; }
  html, body { width: 1200px; height: 1199px; overflow: hidden; background: var(--bg); }
  .canvas { position: relative; width: 1200px; height: 1199px; }
  .card {
    position: absolute; left: 246px; width: 736px; height: 420px; overflow: hidden;
    box-shadow: 0 10px 28px rgba(0,0,0,0.18);
  }
  .card-front { top: 137px; background: linear-gradient(180deg, var(--white), var(--paper)); }
  .card-back { top: 600px; }

  .offer-band {
    position: absolute; left: 0; top: 34px; width: 477px; height: 118px;
    background: linear-gradient(90deg, var(--green-deep), var(--green));
    color: var(--white); font-family: "Montserrat", sans-serif; font-weight: 700;
    padding: 10px 0 0 26px;
  }
  .offer-line { font-size: 37px; line-height: 40px; letter-spacing: 0.3px; }
  .offer-amount { color: var(--red); }
  .offer-note { font-size: 15px; margin-top: 5px; }
  .estimate-tab {
    position: absolute; left: 0; top: 152px; width: 227px; height: 37px;
    background: var(--red); clip-path: polygon(0 0, 100% 0, 92% 100%, 0 100%);
    color: var(--white); font-family: "Montserrat", sans-serif; font-weight: 700;
    font-size: 15px; line-height: 37px; padding-left: 26px;
  }
  .brand-name {
    position: absolute; left: 500px; top: 62px; width: 200px; text-align: center;
    font-family: "Montserrat", sans-serif; font-weight: 700; font-size: 24px;
    line-height: 29px; color: var(--green);
  }
  .brand-bar { position: absolute; left: 720px; top: 34px; width: 16px; height: 118px; background: var(--green); }

  .contact-rail {
    position: absolute; left: 27px; top: 227px; width: 34px; height: 148px;
    background: var(--red); border-radius: 17px;
  }
  .contact-list { position: absolute; left: 27px; top: 243px; list-style: none; }
  .contact-item { display: flex; align-items: center; height: 33px; margin-bottom: 7px; }
  .contact-icon { width: 34px; display: flex; justify-content: center; }
  .contact-text {
    width: 304px; height: 33px; background: var(--ink); color: var(--white);
    font-family: "Lato", sans-serif; font-size: 20px; line-height: 33px; padding-left: 18px;
  }
  .address-list { position: absolute; right: 46px; top: 243px; list-style: none; text-align: right; }
  .address-item {
    display: flex; align-items: center; justify-content: flex-end; height: 33px; margin-bottom: 7px;
    font-family: "Lato", sans-serif; font-size: 21px; color: var(--text);
  }
  .address-item svg { margin-left: 14px; }

  .photo-fill {
    position: absolute; inset: 0;
    background: linear-gradient(160deg, #8a7f76 0%, #4a4a4c 40%, #2c2c2e 70%, #9a9ea3 100%);
  }
  .headline-band {
    position: absolute; left: 0; top: 100px; width: 736px; height: 139px;
    background: linear-gradient(90deg, var(--green-deep), var(--green));
    color: var(--white); font-family: "Montserrat", sans-serif; font-weight: 700;
    font-size: 63px; line-height: 68px; text-align: center; padding-top: 3px;
  }
  .advance-banner {
    position: absolute; left: 43px; top: 239px; width: 650px; height: 69px;
    background: var(--red); border-radius: 0 0 40px 40px;
    clip-path: polygon(0 0, 100% 0, 96% 100%, 4% 100%);
    color: var(--white); font-family: "Montserrat", sans-serif; font-weight: 700;
    font-size: 27px; line-height: 69px; text-align: center;
  }
</style>
</head>
<body>
<main class="canvas">
  <section class="card card-front">
    <div class="offer-band">
      <div class="offer-line">UP TO <span class="offer-amount">$6,000</span></div>
      <div class="offer-line">SAME DAY ADVANCE</div>
      <div class="offer-note">ON APPROVED TAX RETURNS!</div>
    </div>
    <div class="estimate-tab">FREE ESTIMATES!</div>
    <div class="brand-name">Ledger One<br>Financial Group</div>
    <div class="brand-bar"></div>

    <div class="contact-rail"></div>
    <ul class="contact-list">
      <li class="contact-item">
        <span class="contact-icon"><svg width="16" height="16" viewBox="0 0 24 24"><path fill="#fff" d="M6.6 10.8a15 15 0 0 0 6.6 6.6l2.2-2.2a1 1 0 0 1 1-.25 11.4 11.4 0 0 0 3.6.6 1 1 0 0 1 1 1V20a1 1 0 0 1-1 1A17 17 0 0 1 3 4a1 1 0 0 1 1-1h3.5a1 1 0 0 1 1 1c0 1.25.2 2.45.6 3.6a1 1 0 0 1-.25 1z"/></svg></span>
        <span class="contact-text">+(555)5555 5555</span>
      </li>
      <li class="contact-item">
        <span class="contact-icon"><svg width="18" height="14" viewBox="0 0 18 14"><rect x="1" y="1" width="16" height="12" fill="none" stroke="#fff" stroke-width="1.6"/><path d="M1 1l8 7 8-7M1 13l6-6M17 13l-6-6" fill="none" stroke="#fff" stroke-width="1.6"/></svg></span>
        <span class="contact-text">www.ledgerone.com</span>
      </li>
      <li class="contact-item">
        <span class="contact-icon"><svg width="18" height="18" viewBox="0 0 20 20" fill="none" stroke="#fff" stroke-width="1.5"><circle cx="10" cy="10" r="8.5"/><ellipse cx="10" cy="10" rx="3.8" ry="8.5"/><path d="M1.5 10h17M3 5.5h14M3 14.5h14"/></svg></span>
        <span class="contact-text">Downtown@ledgerone.com</span>
      </li>
    </ul>
    <ul class="address-list">
      <li class="address-item">Address Line 1 <svg width="14" height="19" viewBox="0 0 14 19"><path fill="#b81d24" d="M7 0a7 7 0 0 1 7 7c0 5-7 12-7 12S0 12 0 7a7 7 0 0 1 7-7z"/><circle cx="7" cy="7" r="2.6" fill="#fff"/></svg></li>
      <li class="address-item">Address Line 1 <svg width="14" height="19" viewBox="0 0 14 19"><path fill="#b81d24" d="M7 0a7 7 0 0 1 7 7c0 5-7 12-7 12S0 12 0 7a7 7 0 0 1 7-7z"/><circle cx="7" cy="7" r="2.6" fill="#fff"/></svg></li>
      <li class="address-item">Address Line 1 <svg width="14" height="19" viewBox="0 0 14 19"><path fill="#b81d24" d="M7 0a7 7 0 0 1 7 7c0 5-7 12-7 12S0 12 0 7a7 7 0 0 1 7-7z"/><circle cx="7" cy="7" r="2.6" fill="#fff"/></svg></li>
    </ul>
  </section>

  <section class="card card-back">
    <div class="photo-fill" role="img" aria-label="Photo of hands on a laptop with floating tax document icons"></div>
    <div class="headline-band">FILE YOUR<br>TAXES HERE</div>
    <div class="advance-banner">UP TO $6,000 SAME DAY ADVANCE</div>
  </section>
</main>
</body>
</html>
```